Redesign current business card for food company

i would like to redesign my business card. our company is food company, our product range from chips, juices, milk and etc (mostly dried food stuff).
I want o keep same logo but , the rest is open to new design.
you can check at our website about our company www.orvelpantry.com

Target Market(s)

most of food company

Industry/Entity Type

Business

Contact Information for Business Card

I want to keep more to blue color...

Colors
3176b5
abd036

Requirements
Must have
• our old logo
Nice to have
• we do not mind to have nice material on bus card in order to accomplish nice design. for example: using spot uv, embossed and etc.

```html
<!DOCTYPE html>
<html lang="en">
<head>
<meta charset="utf-8">
<title>Orvel business card</title>
<link href="https://fonts.googleapis.com/css2?family=Cabin:wght@400;700&display=swap" rel="stylesheet">
<style>
  :root {
    --backdrop: #1c1c1e;
    --blue-deep: #1426b4;
    --blue-mid: #1b5fcf;
    --blue-light: #14a0d2;
    --logo-navy: #1b2a9e;
    --leaf-green: #13b43c;
    --leaf-soft: #8cc83c;
    --white: #ffffff;
  }
  html, body {
    margin: 0;
    padding: 0;
    width: 1200px;
    height: 987px;
    overflow: hidden;
    background: var(--backdrop);
    font-family: "Cabin", Arial, sans-serif;
  }
  .stage {
    position: relative;
    width: 1200px;
    height: 987px;
  }
  .card {
    position: absolute;
    left: 293px;
    width: 615px;
    height: 352px;
    overflow: hidden;
  }
  .card--front { top: 130px; background: var(--white); }
  .card--back {
    top: 505px;
    background: radial-gradient(ellipse 55% 60% at 50% 50%, var(--blue-light) 0%, var(--blue-mid) 55%, var(--blue-deep) 100%);
  }
  .card__wave {
    position: absolute;
    inset: 0;
    width: 615px;
    height: 352px;
  }
  .brand {
    position: absolute;
    display: flex;
    align-items: center;
    gap: 10px;
    font-weight: 700;
    line-height: 1;
    letter-spacing: -1px;
  }
  .brand__dot {
    width: 14px;
    height: 14px;
    border-radius: 50%;
    background: var(--leaf-soft);
  }
  .card--front .brand {
    left: 30px;
    top: 137px;
    font-size: 76px;
    color: var(--logo-navy);
  }
  .card--back .brand {
    left: 0;
    right: 0;
    top: 133px;
    justify-content: center;
    font-size: 92px;
    color: var(--white);
  }
  .contact {
    position: absolute;
    right: 28px;
    top: 65px;
    text-align: right;
    color: var(--white);
  }
  .contact__name {
    margin: 0;
    font-size: 19px;
    font-weight: 700;
    letter-spacing: 0.3px;
  }
  .contact__role {
    margin: 1px 0 0;
    font-size: 16px;
  }
  .contact__address {
    margin: 18px 0 0;
    font-size: 15px;
    font-style: normal;
    line-height: 21px;
  }
  .contact__lines {
    list-style: none;
    margin: 11px 0 0;
    padding: 0;
    font-size: 15px;
  }
  .contact__lines li {
    display: flex;
    justify-content: flex-end;
    align-items: center;
    gap: 8px;
    height: 23.5px;
  }
  .contact__lines svg {
    width: 15px;
    height: 15px;
    fill: var(--white);
  }
</style>
</head>
<body>
<main class="stage">

  <section class="card card--front" aria-label="Business card front">
    <svg class="card__wave" viewBox="0 0 615 352" aria-hidden="true">
      <defs>
        <radialGradient id="panelGlow" cx="0.72" cy="0.55" r="0.6">
          <stop offset="0" stop-color="#1690d6"/>
          <stop offset="0.6" stop-color="#1a55cc"/>
          <stop offset="1" stop-color="#1530b8"/>
        </radialGradient>
      </defs>
      <path d="M386,0 C338,5 325,120 305,220 C287,310 238,352 186,352 L615,352 L615,0 Z" fill="var(--leaf-green)"/>
      <path d="M398,0 C350,5 338,120 318,220 C300,310 252,352 200,352 L615,352 L615,0 Z" fill="url(#panelGlow)"/>
    </svg>

    <div class="brand"><span>orvel</span><span class="brand__dot"></span></div>

    <div class="contact">
      <p class="contact__name">Daniel Whitcombe</p>
      <p class="contact__role">President</p>
      <address class="contact__address">
        Orvel Enterprises Corp.<br>
        2410 Harlan Ave.<br>
        Corvale CA 90418
      </address>
      <ul class="contact__lines">
        <li>555 214 3080
          <svg viewBox="0 0 24 24" aria-label="Phone"><path d="M6.6 10.8a15 15 0 0 0 6.6 6.6l2.2-2.2a1 1 0 0 1 1-.25 11.4 11.4 0 0 0 3.6.57 1 1 0 0 1 1 1V20a1 1 0 0 1-1 1A17 17 0 0 1 3 4a1 1 0 0 1 1-1h3.5a1 1 0 0 1 1 1c0 1.25.2 2.45.57 3.57a1 1 0 0 1-.25 1z"/></svg>
        </li>
        <li>555 730 4192
          <svg viewBox="0 0 24 24" aria-label="Mobile"><path d="M7 1h10a2 2 0 0 1 2 2v18a2 2 0 0 1-2 2H7a2 2 0 0 1-2-2V3a2 2 0 0 1 2-2zm0 3v15h10V4z"/></svg>
        </li>
        <li>555 214 3081
          <svg viewBox="0 0 24 24" aria-label="Fax"><path d="M6 2h12v6H6zM3 9h18a1 1 0 0 1 1 1v8h-4v4H6v-4H2v-8a1 1 0 0 1 1-1zm5 7v4h8v-4z"/></svg>
        </li>
        <li>Daniel@orvelpantry.com
          <svg viewBox="0 0 24 24" aria-label="Email"><path d="M2 5h20v14H2zm2 2v.5l8 5 8-5V7l-8 5z"/></svg>
        </li>
        <li>www.orvelpantry.com
          <svg viewBox="0 0 24 24" aria-label="Website"><path d="M12 2a10 10 0 1 0 0 20 10 10 0 0 0 0-20zm-1 17.9A8 8 0 0 1 4.2 10.2L9 15v1a2 2 0 0 0 2 2zm6.9-2.5A2 2 0 0 0 16 16h-1v-3a1 1 0 0 0-1-1H8v-2h2a1 1 0 0 0 1-1V7h2a2 2 0 0 0 2-2v-.4a8 8 0 0 1 2.9 12.8z"/></svg>
        </li>
      </ul>
    </div>
  </section>

  <section class="card card--back" aria-label="Business card back">
    <div class="brand"><span>orvel</span><span class="brand__dot"></span></div>
  </section>

</main>
</body>
</html>
```